Business Card Design

We are a commercial real estate brokerage in San Francisco, leasing office buildings downtown.
I would like a clean, elegant look. Simple but powerful .

Industry/Entity Type

Business

Contact Information for Business Card

Derek Holloway
lic# 07258143
415.555.0172
derek@velt-commercial.example
velt-commercial.example

```html
<!DOCTYPE html>
<html lang="en">
<head>
<meta charset="utf-8">
<title>Velt Commercial – Business Card</title>
<link rel="stylesheet" href="https://fonts.googleapis.com/css2?family=Roboto:wght@400;500;700&display=swap">
<style>
  :root {
    --backdrop: #e9e6e1;
    --card: #ffffff;
    --slate: #72819b;
    --slate-dark: #66758f;
    --ink: #3c3c3c;
    --icon: #8a8a8a;
  }
  * { margin: 0; padding: 0; box-sizing: border-box; }
  html, body {
    width: 1200px; height: 695px; overflow: hidden;
    background: var(--backdrop);
    font-family: "Roboto", Arial, sans-serif;
  }
  .card {
    position: absolute; left: 80px; top: 41px;
    width: 1040px; height: 612px;
    background: var(--card);
    box-shadow: 0 6px 22px rgba(0,0,0,0.12);
  }
  .agent { position: absolute; left: 492px; top: 62px; color: var(--slate); }
  .agent-name { font-size: 32px; font-weight: 400; line-height: 1.2; }
  .agent-license { font-size: 26px; font-weight: 400; line-height: 1.3; }
  .brand { position: absolute; left: 330px; top: 236px; display: flex; align-items: center; gap: 30px; }
  .brand-square { width: 104px; height: 104px; background: var(--ink); }
  .brand-name { color: var(--slate-dark); font-weight: 500; line-height: 1; }
  .brand-name .primary { display: block; font-size: 84px; letter-spacing: 1px; }
  .brand-name .secondary { display: block; font-size: 36px; letter-spacing: 1px; margin-top: 6px; }
  .contacts { position: absolute; left: 470px; top: 454px; list-style: none; }
  .contacts li {
    display: flex; align-items: center; gap: 8px;
    height: 32px; font-size: 26px; font-weight: 700; color: var(--slate);
  }
  .contacts svg { width: 16px; height: 16px; flex: none; }
</style>
</head>
<body>
  <main class="card">
    <div class="agent">
      <p class="agent-name">Derek Holloway</p>
      <p class="agent-license">lic# 07258143</p>
    </div>

    <div class="brand">
      <div class="brand-square"></div>
      <p class="brand-name"><span class="primary">VELT</span><span class="secondary">COMMERCIAL</span></p>
    </div>

    <ul class="contacts">
      <li>
        <svg viewBox="0 0 16 16" aria-hidden="true"><circle cx="8" cy="8" r="7.5" fill="var(--icon)"/><path d="M5.5 4.5l1.5 0 .6 2-1 .8a5 5 0 0 0 2.1 2.1l.8-1 2 .6 0 1.5c-3.5.3-6.3-2.5-6-6z" fill="#fff"/></svg>
        <span>415.555.0172</span>
      </li>
      <li>
        <svg viewBox="0 0 16 16" aria-hidden="true"><circle cx="8" cy="8" r="7.5" fill="var(--icon)"/><circle cx="8" cy="8" r="2" fill="none" stroke="#fff" stroke-width="1.3"/><path d="M10 6v3a1.2 1.2 0 0 0 2.4 0V8a4.4 4.4 0 1 0-1.8 3.5" fill="none" stroke="#fff" stroke-width="1.3"/></svg>
        <span>derek@velt-commercial.example</span>
      </li>
      <li>
        <svg viewBox="0 0 16 16" aria-hidden="true"><circle cx="8" cy="8" r="7.5" fill="var(--icon)"/><g fill="none" stroke="#fff" stroke-width="1"><circle cx="8" cy="8" r="5"/><ellipse cx="8" cy="8" rx="2.2" ry="5"/><path d="M3 8h10"/></g></svg>
        <span>velt-commercial.example</span>
      </li>
    </ul>
  </main>
</body>
</html>
```